Vantoq Business Card Project showing the logo and a marbo image on the rear

Design a whacky but professional business card, the logo is for the front and the Marbo image is for the rear. Happy to consider other open source Marbo Images if the designer wants to select one from the web. Vantoq is a competitor to OMB.com.au and Pellory.com.au and is based around every property in Australia

Target Market(s)

Business

Contact Information for Business Card

Name, Title, Email, Web, Phone Number

Font styles to use
Other font styles liked:
• avenir

Requirements
Must have
• Image on Back logo on front
Nice to have
• Happy to consider other images on rear, preftably Colin Marbo. Image supplied I own, we can use open source other Marbo Images

```html
<!DOCTYPE html>
<html lang="en">
<head>
<meta charset="utf-8">
<title>Vantoq Business Card</title>
<link rel="stylesheet" href="https://fonts.googleapis.com/css2?family=Jost:wght@600&family=Poppins:wght@400;600&display=swap">
<style>
  :root {
    --backdrop: #1f1f1f;
    --card-white: #f1f1f1;
    --ink: #151515;
    --accent: #ef8a16;
    --sky-day: #f08a12;
    --sky-night: #3a3a3c;
    --city-pink: #e6428f;
    --city-green: #a6cc2a;
    --city-blue: #3fa3d8;
    --street: #4cb8c9;
  }
  * { box-sizing: border-box; margin: 0; padding: 0; }
  html, body { width: 1200px; height: 1138px; overflow: hidden; }
  body {
    background: var(--backdrop);
    font-family: "Poppins", sans-serif;
    position: relative;
  }
  .card {
    position: absolute;
    left: 276px;
    width: 620px;
    height: 376px;
    border-radius: 16px;
    overflow: hidden;
  }
  .card--rear { top: 185px; }
  .card--front { top: 607px; background: var(--card-white); }

  .artwork-full {
    width: 100%;
    height: 100%;
    background:
      linear-gradient(180deg, transparent 0%, transparent 40%, rgba(230,66,143,.85) 55%, rgba(166,204,42,.85) 70%, rgba(63,163,216,.9) 85%, var(--street) 100%),
      linear-gradient(90deg, var(--sky-day) 0%, var(--sky-day) 49.5%, var(--sky-night) 50.5%, var(--sky-night) 100%);
  }

  .brand {
    position: absolute;
    left: 40px;
    top: 48px;
    display: flex;
    align-items: center;
    gap: 18px;
  }
  .brand-mark {
    width: 28px;
    height: 28px;
    background: var(--accent);
  }
  .brand-name {
    font-family: "Jost", sans-serif;
    font-weight: 600;
    font-size: 58px;
    line-height: 1;
    color: var(--ink);
    letter-spacing: 0.5px;
  }

  .person {
    position: absolute;
    left: 38px;
    top: 193px;
  }
  .person-name {
    font-weight: 600;
    font-size: 22px;
    color: var(--accent);
    line-height: 1.2;
  }
  .person-title {
    font-size: 15.5px;
    color: var(--ink);
    line-height: 1.4;
  }

  .contact-list {
    position: absolute;
    left: 362px;
    top: 170px;
    list-style: none;
  }
  .contact-list li {
    display: flex;
    align-items: center;
    gap: 14px;
    font-size: 16px;
    color: var(--ink);
    height: 24px;
  }
  .contact-list svg { width: 14px; height: 14px; flex: none; }

  .artwork-strip {
    position: absolute;
    left: 0;
    bottom: 0;
    width: 100%;
    height: 98px;
    background:
      linear-gradient(180deg, transparent 0%, var(--city-blue) 12%, var(--city-pink) 40%, var(--city-green) 65%, #e9c82e 82%, var(--street) 100%);
    opacity: .95;
  }
</style>
</head>
<body>
  <section class="card card--rear">
    <div class="artwork-full" role="img" aria-label="Colourful naive city illustration: cheerful painted buildings under a half day, half night sky with a train along the bottom"></div>
  </section>

  <section class="card card--front">
    <div class="brand">
      <span class="brand-mark"></span>
      <span class="brand-name">Vantoq</span>
    </div>

    <div class="person">
      <p class="person-name">Leo Darnell</p>
      <p class="person-title">Founder &amp; CEO</p>
    </div>

    <ul class="contact-list">
      <li>
        <svg viewBox="0 0 14 14"><path fill="#ef8a16" d="M1 5c0-2 3-3 6-3s6 1 6 3l-2 1-1-2H4L3 6zM3 7h8l1 5H2z"/></svg>
        (00) 4815 7720
      </li>
      <li>
        <svg viewBox="0 0 14 14"><rect x="1" y="3" width="12" height="8" fill="#ef8a16"/><path d="M1 3l6 5 6-5" fill="none" stroke="#f1f1f1" stroke-width="1.2"/></svg>
        darnell@vantoq.com
      </li>
      <li>
        <svg viewBox="0 0 14 14"><circle cx="7" cy="7" r="6" fill="#ef8a16"/><path d="M1 7h12M7 1c-3 3-3 9 0 12M7 1c3 3 3 9 0 12" fill="none" stroke="#f1f1f1" stroke-width=".9"/></svg>
        www.vantoq.com
      </li>
    </ul>

    <div class="artwork-strip" role="img" aria-label="Strip of colourful naive city buildings with a train, repeated along the card edge"></div>
  </section>
</body>
</html>
```